redesign my website bluekeelvoyages.net and make it user friendly

I already have a website, bluekeelvoyages.net, and want a redesign in WordPress with Elementor Pro, using the same text/content. The goal is to improve:

Design quality (colors, fonts, spacing, visual flow)
User experience (easy navigation, clear offers)
Conversion readiness (calls-to-action, trust signals, booking flow)
Technical side (SEO basics, fast speed, full mobile responsiveness)

The site should look modern, clean, fun, engaging, interactive and optimized for speed and usability.

I would like the 11 page to be consolidate dto 6 as follows: Home (main landing, highlights)

Sailboat Trips (all packages, itineraries, pricing)
Boats (fleet details, features, photos)
How It Works (booking process, FAQs, travel info, what to expect)
Blog
Contact Us (form, WhatsApp, phone, etc.)

Target Market(s)

sailboat trip customers for San Blas Islands in Panama

Industry/Entity Type

Travel, Boat Tour Agency

Coding

Coded - Design and coding required

Number of Pages Required

3 page

Font styles to use
Sans Serif
Other font styles liked:
• Oswalg and sans serif

Colors
0054AA
0677BA
7BADD7
CADEEF
E8F1F8
0094D4
00A9DD
6FCCEA
C7EBF8
E9F6FB
FFC000
F8CF3A
FAE287
FDF2CF
FEFAEE
F0912C
F2A743
F7CA91
FBE8D2
FDF5EE

Requirements
Must have
• Home (main landing, highlights) Sailboat Trips (all packages, itineraries, pricing) Boats (fleet details, features, photos) How It Works (booking process, FAQs, travel info, what to expect) Blog (updates, travel tips, inspiration) Contact Us (form, WhatsApp, phone, etc.)
Nice to have
• I want it to look professionla and be very user friendy to entice people to contact me to book boat trips
Should not have
• a store

```html
<!DOCTYPE html>
<html lang="en">
<head>
<meta charset="utf-8">
<title>Blue Keel Voyages – San Blas Islands Sailing</title>
<link href="https://fonts.googleapis.com/css2?family=Oswald:wght@500&family=Outfit:wght@300;400;500&family=Manrope:wght@400;500;600;700&display=swap" rel="stylesheet">
<style>
:root{
  --blue:#0054AA;
  --blue-dark:#0a3f8c;
  --orange:#F0912C;
  --gold:#FFC000;
  --ink:#1f2430;
  --muted:#555b66;
  --band:#eef1f6;
  --line:#b9bfc8;
  --footer:#1c1c1c;
  --footer-deep:#141414;
}
*{box-sizing:border-box;margin:0;padding:0}
html,body{width:1200px;height:4535px;overflow:hidden}
body{position:relative;background:#fff;font-family:'Manrope',sans-serif;color:var(--ink)}
.abs{position:absolute}
.btn{position:absolute;background:var(--blue);color:#fff;font:600 15px 'Manrope',sans-serif;text-transform:uppercase;display:flex;align-items:center;justify-content:center;border-radius:4px;letter-spacing:.2px}
.photo{position:absolute}
.orange{color:var(--orange)}
.dash{display:inline-block;width:36px;height:2px;background:var(--orange);vertical-align:middle}
.section-title{position:absolute;left:0;width:1200px;text-align:center;font:400 34px 'Outfit',sans-serif;color:var(--blue)}
.section-title .dash{margin:0 18px}

.topbar{position:absolute;left:0;top:0;width:1200px;height:35px;background:var(--blue);color:#fff;font:500 12.5px 'Manrope',sans-serif;text-transform:uppercase}
.topbar .call{position:absolute;left:112px;top:10px;color:var(--orange);display:flex;align-items:center;gap:8px}
.topbar .call b{color:#fff;font-weight:500}
.topbar .links{position:absolute;right:90px;top:10px;display:flex;gap:18px}
.brand{position:absolute;display:flex;align-items:center;gap:12px;font:500 26px 'Oswald',sans-serif;letter-spacing:2px;color:var(--blue-dark)}
.brand i{width:26px;height:26px;border-radius:50%;background:var(--blue);display:block}
.nav{position:absolute;left:458px;top:73px;display:flex;gap:32px;font:500 13px 'Manrope',sans-serif;text-transform:uppercase;color:var(--ink)}
.nav .on{color:var(--blue)}

.hero-title{position:absolute;left:110px;top:140px;font:400 48px/66px 'Outfit',sans-serif;color:var(--blue)}
.hero-sub{position:absolute;left:110px;top:290px;font:400 22px 'Outfit',sans-serif}
.band-gray{position:absolute;left:0;width:1200px;background:var(--band)}

.about-title{position:absolute;left:604px;top:812px;font:400 34px 'Outfit',sans-serif;color:var(--blue)}
.about-title .dash{margin-left:16px}
.about-text{position:absolute;left:604px;top:876px;width:470px;font:400 13.5px/31px 'Manrope',sans-serif;color:#333}

.tour{position:absolute;top:1518px;width:308px;height:456px;border-radius:16px;overflow:hidden}
.tour-tag{position:absolute;background:#fff;border-radius:10px;display:flex;align-items:center;gap:12px;font:600 12.5px/26px 'Manrope',sans-serif;text-transform:uppercase;color:var(--ink);padding:0 16px}
.tour-tag > span:not(.arrow){white-space:nowrap}
.tour-tag .arrow{margin-left:auto;flex:none;width:40px;height:40px;border-radius:50%;border:1px solid var(--line);display:flex;align-items:center;justify-content:center}

.boat{position:absolute;top:2331px;width:360px;height:572px;background:#fff;border:1px solid #e1e4ea;border-radius:14px;text-align:center}
.boat .pic{position:absolute;left:12px;top:10px;width:334px;height:234px;border-radius:12px}
.boat .specs{position:absolute;left:14px;right:14px;top:258px;display:flex;justify-content:center;gap:30px;font:500 11.5px 'Manrope',sans-serif;color:#333;padding-bottom:16px;border-bottom:1px solid #e6e8ee}
.boat .specs span{display:flex;align-items:center;gap:8px}
.boat .kind{position:absolute;left:0;right:0;top:318px;font:600 13px 'Manrope',sans-serif;letter-spacing:.5px}
.boat .name{position:absolute;left:0;right:0;top:346px;font:400 24px 'Outfit',sans-serif;color:var(--blue)}
.boat .tag{position:absolute;left:0;right:0;top:392px;font:500 14px 'Manrope',sans-serif;color:var(--orange)}
.boat .quote{position:absolute;left:24px;right:24px;top:424px;font:400 14px/32px 'Manrope',sans-serif;color:#333;height:64px;overflow:hidden;white-space:nowrap}
.boat .info{position:absolute;left:122px;top:510px;width:116px;height:34px;border:1px solid var(--blue);border-radius:4px;font:600 12px/32px 'Manrope',sans-serif;color:var(--blue)}
.boat.featured{background:var(--blue);border-color:var(--blue)}
.boat.featured .specs,.boat.featured .kind,.boat.featured .name,.boat.featured .quote{color:#fff}
.boat.featured .specs{border-color:rgba(255,255,255,.3)}
.boat.featured .info{color:#fff;border-color:#fff}

.stars{position:absolute;left:0;width:1200px;top:3108px;display:flex;justify-content:center;gap:8px}
.review{position:absolute;left:190px;top:3160px;width:820px;text-align:center;font:400 15px/32px 'Manrope',sans-serif;color:#333}
.qmark{position:absolute;left:186px;top:3120px;font:700 110px/1 'Outfit',sans-serif;color:#c9d5e6}
.dots{position:absolute;left:0;width:1200px;top:3336px;display:flex;justify-content:center;gap:18px}
.dots i{width:10px;height:10px;border-radius:50%;border:1.5px solid var(--blue)}
.dots i.on{background:var(--blue)}

.field{position:absolute;height:46px;border:1.5px solid #8e949d;border-radius:3px;font:500 13px 'Manrope',sans-serif;color:#555;text-transform:uppercase;padding:14px 18px;background:#fff}
.check{position:absolute;top:3955px;display:flex;align-items:center;gap:14px;font:500 13px 'Manrope',sans-serif;color:#555;text-transform:uppercase}
.check i{width:15px;height:15px;border:1.5px solid #555;border-radius:2px}

.footer{position:absolute;left:0;top:4138px;width:1200px;height:332px;background:var(--footer);color:#e6e6e6}
.footer .brand{left:111px;top:56px;color:#fff}
.footer .about{position:absolute;left:111px;top:128px;width:340px;font:400 13.5px/32px 'Manrope',sans-serif}
.footer h4{position:absolute;font:400 22px 'Outfit',sans-serif;color:var(--orange)}
.footer .col{position:absolute;top:108px;font:400 13.5px/36px 'Manrope',sans-serif}
.footer .contact{position:absolute;left:878px;display:flex;align-items:center;gap:16px;font:400 13.5px 'Manrope',sans-serif}
.circle{width:36px;height:36px;border-radius:50%;border:1.5px solid var(--orange);display:flex;align-items:center;justify-content:center}
.copy{position:absolute;left:0;top:4470px;width:1200px;height:65px;background:var(--footer-deep);color:#e6e6e6;font:400 13.5px 'Manrope',sans-serif;display:flex;justify-content:center;align-items:center;gap:18px}
.copy span.sep{width:1px;height:20px;background:#999}
</style>
</head>
<body>

<div class="topbar">
  <div class="call">
    <svg width="13" height="13" viewBox="0 0 24 24"><path fill="#F0912C" d="M6.6 10.8c1.4 2.8 3.8 5.1 6.6 6.6l2.2-2.2c.3-.3.7-.4 1-.2 1.1.4 2.3.6 3.6.6.6 0 1 .4 1 1V20c0 .6-.4 1-1 1C10.6 21 3 13.4 3 4c0-.6.4-1 1-1h3.5c.6 0 1 .4 1 1 0 1.3.2 2.5.6 3.6.1.3 0 .7-.2 1z"/></svg>
    CALL US : <b>+57 300 555 0142</b>
  </div>
  <div class="links"><span>Activities</span><span>|</span><span>Blog</span><span>|</span><span>FAQs</span><span>|</span><span>Contact Us</span></div>
</div>

<div class="brand" style="left:111px;top:64px"><i></i>Blue Keel Voyages</div>
<nav class="nav"><span class="on">Home</span><span>Guna Yala</span><span>Fleet</span><span>About Us</span><span>Book Now</span><span>Pricing</span><span>Itineraries</span></nav>

<div class="band-gray" style="top:558px;height:788px"></div>
<h1 class="hero-title">San Blas Islands:<br><span class="orange">Panama Sailing Vacations.</span></h1>
<p class="hero-sub">Ultimate Beaches &amp; Catamaran Tours</p>
<div class="btn" style="left:927px;top:204px;width:160px;height:42px">Enquiry Now</div>
<div class="photo" role="img" aria-label="Sailboat on calm water with mountains in the background" style="left:111px;top:368px;width:976px;height:376px;border-radius:188px;background:linear-gradient(180deg,#a9c4dc 0%,#c8d9e8 42%,#5e7f9a 56%,#2f5f88 100%)"></div>

<div class="abs" style="left:136px;top:808px;width:348px;height:470px;border:1.5px dashed var(--orange);border-radius:174px"></div>
<div class="photo" role="img" aria-label="Classic sailboat with full white sails heeling in the wind" style="left:146px;top:818px;width:338px;height:452px;border-radius:169px;background:linear-gradient(160deg,#d7e4ef 0%,#8fb0cc 50%,#3f6f98 100%)"></div>
<h2 class="about-title">Who <span class="orange">We</span> Are<span class="dash"></span></h2>
<p class="about-text">We’re sailors and travelers with a love for exploration. When we first arrived in San Blas, its unique beauty and culture left a lasting impression. What began as a stop along our journey soon became something more—we felt a strong connection to this place and a sincere respect for its people, traditions, and way of life. Rather than simply making it our home, we’ve done our best to live in harmony with the environment and the values of the local community.Today, our mission is to share the experience of San Blas with others through safe, sustainable, and memorable sailing adventures.</p>
<div class="btn" style="left:604px;top:1203px;width:144px;height:41px">Learn More</div>

<h2 class="section-title" style="top:1418px"><span class="dash"></span>Discover <span class="orange">Ultimate Panama</span> Sailing Tours<span class="dash"></span></h2>

<div class="tour" role="img" aria-label="Luxury motor yacht cruising on deep blue sea" style="left:111px;background:linear-gradient(170deg,#2f5f84,#1d4463 60%,#163650)">
  <div class="tour-tag" style="left:54px;top:358px;width:242px;height:80px">
    <svg width="34" height="34" viewBox="0 0 34 34" fill="none" stroke="#0054AA" stroke-width="1.6"><path d="M16 4v20M16 6l10 16H16M16 8 8 22h8M4 26h26l-4 4H8z"/></svg>
    <span>Private<br>Charters</span>
    <span class="arrow"><svg width="14" height="14" viewBox="0 0 14 14"><path d="M3 11 11 3M5 3h6v6" stroke="#222" stroke-width="1.5" fill="none"/></svg></span>
  </div>
</div>
<div class="tour" role="img" aria-label="Yacht deck at sunset with warm sky" style="left:445px;background:linear-gradient(180deg,#c3b5b0 0%,#d7a887 45%,#8a6c5c 70%,#3d3a3c 100%)">
  <div class="tour-tag" style="left:54px;top:256px;width:240px;height:184px;display:block;padding:18px 20px;text-transform:none;font-weight:400;font-size:13.5px;line-height:30px">
    <div style="display:flex;align-items:center;gap:14px;text-transform:uppercase;font-weight:600;font-size:13px;margin-bottom:14px">
      <svg width="28" height="30" viewBox="0 0 28 30" fill="none" stroke="#0054AA" stroke-width="1.6"><rect x="3" y="3" width="18" height="24" rx="2"/><path d="M7 9h10M7 14h10M7 19h6M18 22l6-8"/></svg>Shared Charters</div>
    Share the experience with<br>others for a more affordable<br>alternative to a private charter.
  </div>
</div>
<div class="tour" role="img" aria-label="Family enjoying a sailboat trip with white sails behind them" style="left:781px;background:linear-gradient(170deg,#dfe6ec 0%,#a9bccd 40%,#4b6f93 75%,#274c70 100%)">
  <div class="tour-tag" style="left:54px;top:358px;width:242px;height:80px">
    <svg width="40" height="34" viewBox="0 0 40 34" fill="none" stroke="#0054AA" stroke-width="1.6"><path d="M16 4v18M16 6l10 14H16M4 24h32l-4 6H8zM30 4h6v6h-6z"/></svg>
    <span>Family Friendly<br>Boat Trips</span>
    <span class="arrow"><svg width="14" height="14" viewBox="0 0 14 14"><path d="M3 11 11 3M5 3h6v6" stroke="#222" stroke-width="1.5" fill="none"/></svg></span>
  </div>
</div>
<div class="btn" style="left:498px;top:2027px;width:204px;height:42px">Request a Quote</div>

<div class="photo" role="img" aria-label="Catamaran moored in a bay with mountains" style="left:0;top:2155px;width:600px;height:498px;background:linear-gradient(180deg,#c5d3df 0%,#8fa8bc 40%,#3f6e97 70%,#244f77 100%)"></div>
<h2 class="abs" style="left:662px;top:2148px;font:400 34px 'Outfit',sans-serif;color:var(--blue)">Featured <span class="orange">Catamarans</span><span class="dash" style="margin-left:16px"></span></h2>
<div class="btn" style="left:663px;top:2228px;width:241px;height:42px">See All Boats &amp; Prices</div>

<div class="boat" style="left:111px">
  <div class="pic" role="img" aria-label="White catamaran anchored in turquoise water beside a beach" style="background:linear-gradient(160deg,#e9e2cf 0%,#5fc2c6 35%,#1e8ea3 70%,#0f5f7c 100%)"></div>
  <div class="specs"><span><svg width="16" height="14" viewBox="0 0 16 14"><path fill="#0054AA" d="M1 13V2h3v5h10v6z"/></svg>42 FT</span><span><svg width="14" height="14" viewBox="0 0 14 14"><path fill="#0054AA" d="M7 1v10H2zM1 12h12v1H1z"/></svg>3 CABIN</span><span><svg width="18" height="14" viewBox="0 0 18 14"><circle cx="9" cy="4" r="3" fill="#0054AA"/><circle cx="3.5" cy="5" r="2" fill="#0054AA"/><circle cx="14.5" cy="5" r="2" fill="#0054AA"/><path fill="#0054AA" d="M3 13c0-3 2.5-5 6-5s6 2 6 5z"/></svg>8 GUEST</span></div>
  <div class="kind">CATAMARAN</div>
  <div class="name">Marea 42</div>
  <div class="tag">Service that exceeds all expectations!</div>
  <div class="quote">“We started as strangers and left as friends!<br>The crew made sure everyone felt welcome,</div>
  <div class="info">INFO &amp; PRICE</div>
</div>

<div class="boat featured" style="left:507px">
  <div class="pic" role="img" aria-label="Catamaran near a small palm-covered island" style="background:linear-gradient(170deg,#3c83b8 0%,#5f9e7a 42%,#26a0a9 60%,#0f6c8a 100%)"></div>
  <div class="specs"><span><svg width="16" height="14" viewBox="0 0 16 14"><path fill="#fff" d="M1 13V2h3v5h10v6z"/></svg>55 FT</span><span><svg width="14" height="14" viewBox="0 0 14 14"><path fill="#fff" d="M7 1v10H2zM1 12h12v1H1z"/></svg>4 CABIN</span><span><svg width="18" height="14" viewBox="0 0 18 14"><circle cx="9" cy="4" r="3" fill="#fff"/><circle cx="3.5" cy="5" r="2" fill="#fff"/><circle cx="14.5" cy="5" r="2" fill="#fff"/><path fill="#fff" d="M3 13c0-3 2.5-5 6-5s6 2 6 5z"/></svg>8 GUEST</span></div>
  <div class="kind">CATAMARAN</div>
  <div class="name">Tidewind 55F</div>
  <div class="tag">Luxury and elegance on water!</div>
  <div class="quote">“It was like having our own private island, but<br>with the luxury of a floating home</div>
  <div class="info">INFO &amp; PRICE</div>
</div>

<div class="boat" style="left:901px">
  <div class="pic" role="img" aria-label="Aerial view of a sailing catamaran on open blue sea" style="background:linear-gradient(160deg,#2f78a6 0%,#1f6a98 50%,#174f7a 100%)"></div>
  <div class="specs" style="justify-content:flex-start;padding-left:24px"><span><svg width="16" height="14" viewBox="0 0 16 14"><path fill="#0054AA" d="M1 13V2h3v5h10v6z"/></svg>20 FT</span><span><svg width="14" height="14" viewBox="0 0 14 14"><path fill="#0054AA" d="M7 1v10H2zM1 12h12v1H1z"/></svg>4 CABIN</span><span><svg width="18" height="14" viewBox="0 0 18 14"><circle cx="9" cy="4" r="3" fill="#0054AA"/><circle cx="3.5" cy="5" r="2" fill="#0054AA"/><circle cx="14.5" cy="5" r="2" fill="#0054AA"/><path fill="#0054AA" d="M3 13c0-3 2.5-5 6-5s6 2 6 5z"/></svg>9 GUEST</span></div>
  <div class="kind">CATAMARAN</div>
  <div class="name">Tidewind 55S</div>
  <div class="tag">Safest family fun at sea!</div>
  <div class="quote" style="text-align:left;left:28px">“The best family trip we’ve ever had! Our kids<br>couldn’t get enough of exploring the islands</div>
  <div class="info">INFO &amp; PRICE</div>
</div>

<div class="band-gray" style="top:2991px;height:408px"></div>
<h2 class="section-title" style="top:3042px"><span class="dash"></span>What <span class="orange">They</span> Say<span class="dash"></span></h2>
<div class="stars">
  <svg width="18" height="18" viewBox="0 0 24 24"><path fill="#F8B620" d="M12 2l3 7 7 .6-5.3 4.7 1.6 7.2L12 17.8 5.7 21.5l1.6-7.2L2 9.6 9 9z"/></svg>
  <svg width="18" height="18" viewBox="0 0 24 24"><path fill="#F8B620" d="M12 2l3 7 7 .6-5.3 4.7 1.6 7.2L12 17.8 5.7 21.5l1.6-7.2L2 9.6 9 9z"/></svg>
  <svg width="18" height="18" viewBox="0 0 24 24"><path fill="#F8B620" d="M12 2l3 7 7 .6-5.3 4.7 1.6 7.2L12 17.8 5.7 21.5l1.6-7.2L2 9.6 9 9z"/></svg>
  <svg width="18" height="18" viewBox="0 0 24 24"><path fill="#F8B620" d="M12 2l3 7 7 .6-5.3 4.7 1.6 7.2L12 17.8 5.7 21.5l1.6-7.2L2 9.6 9 9z"/></svg>
  <svg width="18" height="18" viewBox="0 0 24 24"><path fill="#F8B620" d="M12 2l3 7 7 .6-5.3 4.7 1.6 7.2L12 17.8 5.7 21.5l1.6-7.2L2 9.6 9 9z"/></svg>
</div>
<div class="qmark">“</div>
<p class="review">My family and I sailed with Captain Rafa and Lio on the Brisa Azul for 4 days. It was the best possible experience. Rafa took care of our EVERY needs as a family. Moreover, because we were traveling with my elderly parents as well as younger kids, we needed a wide range of travel accommodations. Clara from Blue Keel Voyages did EVERYTHING. She was very responsive, and professional and took care of all of our requests, down to every last detail. I would absolutely book with her again and would recommend all my friends to do as as well. 10/10 experience!</p>
<div class="dots"><i></i><i class="on"></i><i></i><i></i></div>

<h2 class="section-title" style="top:3476px"><span class="dash"></span>Book <span class="orange">An</span> Adventure<span class="dash"></span></h2>
<div class="field" style="left:111px;top:3566px;width:311px">Name*</div>
<div class="field" style="left:443px;top:3566px;width:312px">Email*</div>
<div class="field" style="left:776px;top:3566px;width:311px">Whatsapp Number*</div>
<div class="field" style="left:111px;top:3652px;width:311px">Number of Passengers</div>
<div class="field" style="left:443px;top:3652px;width:312px">Number of Days</div>
<div class="field" style="left:776px;top:3652px;width:311px">Date</div>
<div class="field" style="left:111px;top:3737px;width:976px">What type of experience are you looking for? (Check all that apply)
  <svg class="abs" style="right:18px;top:19px" width="10" height="6" viewBox="0 0 10 6"><path d="M0 0h10L5 6z" fill="#222"/></svg></div>
<div class="field" style="left:111px;top:3823px;width:976px;height:99px">Message</div>
<div class="check" style="left:375px"><i></i>Private Charter</div>
<div class="check" style="left:658px"><i></i>Shared Charter</div>
<div class="btn" style="left:519px;top:4017px;width:162px;height:40px">Send Message</div>

<footer class="footer">
  <div class="brand"><i></i>Blue Keel Voyages</div>
  <p class="about">Discover unforgettable catamaran and sailboat adventures in Guna Yala (San Blas), Panama. Blue Keel Voyages LLC offers all-inclusive island-hopping, snorkeling, and immersive cultural experiences—trusted by travelers worldwide.</p>
  <h4 style="left:554px;top:56px">Explore</h4>
  <div class="col" style="left:556px">Home<br>Fleet<br>About Us<br>Contact<br>Pricing</div>
  <div class="col" style="left:693px">Guna Yala<br>Itineraries<br>Activities<br>Book Now<br>Blog</div>
  <h4 style="left:877px;top:56px">Get in Touch</h4>
  <div class="contact" style="top:104px"><span class="circle"><svg width="14" height="14" viewBox="0 0 24 24"><path fill="#F0912C" d="M6.6 10.8c1.4 2.8 3.8 5.1 6.6 6.6l2.2-2.2c.3-.3.7-.4 1-.2 1.1.4 2.3.6 3.6.6.6 0 1 .4 1 1V20c0 .6-.4 1-1 1C10.6 21 3 13.4 3 4c0-.6.4-1 1-1h3.5c.6 0 1 .4 1 1 0 1.3.2 2.5.6 3.6.1.3 0 .7-.2 1z"/></svg></span>+57 300 555 0142</div>
  <div class="contact" style="top:164px"><span class="circle"><svg width="14" height="11" viewBox="0 0 14 11"><rect x=".5" y=".5" width="13" height="10" rx="1" fill="none" stroke="#F0912C"/><path d="M1 1l6 5 6-5" fill="none" stroke="#F0912C"/></svg></span>hello@bluekeelvoyages.net</div>
  <div class="contact" style="top:230px;gap:8px"><span class="circle" style="width:32px;height:32px"></span><span class="circle" style="width:32px;height:32px"></span><span class="circle" style="width:32px;height:32px"></span></div>
</footer>
<div class="copy">Copyright 2025 © Blue Keel Voyages<span class="sep"></span>Privacy Policy<span class="sep"></span>Terms &amp; Conditions</div>

</body>
</html>
```